I need an Oakline Office selling website

My Oakline Office store is driven by creativity and innovation. With this i am searching for an industry standard website for my Oakline Office and items selling website. I sell a wide range of Oakline Office items such as chairs, tables, burglary, cotton, wardrobe, etc. There will be a category for each of the items i sell. My business is based in the United States and services only US based residents. I don't accept online payments and customers are to pay on delivery of items. The website is to have images of the items i sell. I would like brown, black and golden colors because those are the colors furniture mostly make use of. Designs submitted should be unique.

Industry/Entity Type

Furniture Store

Coding

Coded - Design and coding required

```html
<!DOCTYPE html>
<html lang="en">
<head>
<meta charset="utf-8">
<title>Oakline Office</title>
<link rel="stylesheet" href="https://fonts.googleapis.com/css2?family=Roboto:wght@400;500;700&family=Arimo:wght@400;700&display=swap">
<style>
:root{
  --gold:#b99a3a;
  --ink:#111111;
  --text:#555555;
  --muted:#888888;
  --line:#dddddd;
  --panel:#efefef;
  --bar:#f1f1f1;
  --white:#ffffff;
}
*{box-sizing:border-box;margin:0;padding:0}
html,body{width:1200px;height:2663px;overflow:hidden;background:var(--white)}
body{position:relative;font-family:"Arimo",Arial,sans-serif;color:var(--text)}
.abs{position:absolute}
.topbar{left:0;top:0;width:1200px;height:53px;background:var(--bar)}
.social{display:flex;gap:8px}
.social .net{width:34px;height:34px;border-radius:50%;border:1.5px solid #777;display:flex;align-items:center;justify-content:center;background:var(--white)}
.social .net:first-child{background:#666;border-color:#666}
.social .net:first-child svg *{stroke:#fff;fill:#fff}
.topbar .social{position:absolute;left:78px;top:9px}
.contact-top{position:absolute;right:78px;top:0;height:53px;display:flex;align-items:center;gap:24px;font-size:15px;color:#444}
.contact-top div{display:flex;align-items:center;gap:9px}
.nav-rule{left:78px;width:1044px;height:2px;background:#e2e2e2}
.nav{top:107px;height:62px;display:flex;align-items:center;font-family:"Roboto",sans-serif;font-size:16px;color:#666}
.nav a{color:#666;text-decoration:none;padding:0 29px;border-right:1px solid #e2e2e2;line-height:30px}
.nav a:last-child{border-right:none}
.nav-left{left:128px}
.nav-right{left:680px}
.brand-badge{left:525px;top:58px;width:150px;height:150px;border-radius:50%;border:2px dotted #555;background:var(--white);display:flex;align-items:center;justify-content:center;text-align:center;font-family:"Roboto",sans-serif;font-size:20px;font-weight:500;color:var(--ink);line-height:1.2}
.hero{left:78px;top:218px;width:1044px;height:469px;background:linear-gradient(120deg,#d9d9d4 0%,#b8b8b2 45%,#4a4a48 75%,#1e1e1e 100%)}
.hero-arrow{top:418px;width:34px;height:66px;background:rgba(80,80,80,.7);display:flex;align-items:center;justify-content:center}
.arrow-l{left:78px;border-radius:0 33px 33px 0}
.arrow-r{left:1088px;border-radius:33px 0 0 33px}
.section-title{left:0;width:1200px;text-align:center;font-family:"Roboto",sans-serif;font-size:42px;color:var(--ink);font-weight:400}
.intro{left:150px;top:803px;width:900px;text-align:center;font-size:15px;line-height:28px;color:var(--text)}
.btn{background:var(--gold);color:var(--white);font-family:"Roboto",sans-serif;display:flex;align-items:center;justify-content:center;text-transform:uppercase}
.know-more{left:509px;top:895px;width:180px;height:57px;font-size:21px}
.divider{left:78px;top:1017px;width:1044px;height:5px;background:#efefef}
.product{width:250px;height:311px;background:var(--panel);border:1px solid var(--line)}
.product .photo{position:absolute;left:50%;transform:translateX(-50%);top:22px;width:150px;height:180px;border-radius:3px}
.product .name{position:absolute;left:9px;top:238px;font-family:"Roboto",sans-serif;font-size:26px;color:var(--ink)}
.product .price{position:absolute;left:11px;top:272px;font-family:"Roboto",sans-serif;font-size:19px;color:var(--gold)}
.product .detail{position:absolute;right:0;top:238px;width:119px;height:57px;font-size:21px}
.ph-chair{background:linear-gradient(160deg,#4a4a4a 0%,#262626 60%,#151515 100%)}
.ph-cloth{width:170px!important;height:160px!important;top:32px!important;background:linear-gradient(160deg,#3e5f8e 0%,#b84040 30%,#2f7a52 55%,#e9e9e9 85%)}
.ph-safe{width:140px!important;height:130px!important;top:50px!important;background:linear-gradient(160deg,#3a3a3a 0%,#1c1c1c 100%)}
.ph-table{width:150px!important;height:140px!important;top:45px!important;background:linear-gradient(160deg,#453b36 0%,#221c19 100%)}
.ph-scarf{width:170px!important;height:150px!important;top:35px!important;background:linear-gradient(160deg,#d8d8d8 0%,#bdbdbd 55%,#cfcfcf 100%)}
.ph-wood{width:80px!important;height:170px!important;top:26px!important;background:linear-gradient(90deg,#3a2a22 0%,#4a372d 50%,#3a2a22 100%)}
.newsletter{left:78px;top:1860px;width:1044px;height:165px;background:var(--panel)}
.newsletter .label{position:absolute;left:25px;top:64px;font-family:"Roboto",sans-serif;font-size:28px;color:#444}
.newsletter .email{position:absolute;left:332px;top:53px;width:467px;height:61px;background:var(--white);border:1px solid #d5d5d5;font-size:15px;color:#777;padding:0 18px;display:flex;align-items:center}
.newsletter .subscribe{position:absolute;left:810px;top:53px;width:207px;height:61px;font-size:21px}
.work{top:2089px;height:208px;border:1px solid var(--line)}
.work-a{left:78px;width:332px;background:linear-gradient(135deg,#f4f6f7,#c9d6dc 60%,#e8ecee)}
.work-b{left:435px;width:330px;background:linear-gradient(135deg,#f6f6f4,#e3e3de 60%,#f2f2ef)}
.work-c{left:790px;width:332px;background:linear-gradient(135deg,#eeeeec,#c8c6c0 55%,#8a7d70 80%,#dcdcd8)}
.work-b .caption{position:absolute;left:0;top:65px;width:100%;text-align:center;font-family:"Roboto",sans-serif;font-size:24px;color:var(--ink)}
.work-b .view{position:absolute;left:112px;top:110px;width:106px;height:50px;font-size:21px}
.footer-rule{left:78px;top:2359px;width:1044px;height:4px;background:#999}
.f-col{top:2396px}
.f-col h4{font-family:"Roboto",sans-serif;font-size:15px;font-weight:700;color:#222;margin-bottom:20px}
.f-col ul{list-style:none}
.f-col li{font-size:13px;line-height:23px;color:#555;display:flex;align-items:center;gap:12px}
.f-col li::before{content:"";width:5px;height:5px;border-top:1.5px solid #555;border-right:1.5px solid #555;transform:rotate(45deg)}
.touch-row{display:flex;gap:16px;align-items:flex-start;font-size:14px;color:#555;margin-bottom:14px}
.touch-row svg{flex:none;margin-top:2px}
.touch-row strong{display:block;font-family:"Roboto",sans-serif;font-size:15px;font-weight:500;color:#333;margin-bottom:3px}
.footer-badge{left:940px;top:2389px;width:124px;height:124px;border-radius:50%;border:2px dotted #555;display:flex;align-items:center;justify-content:center;text-align:center;font-family:"Roboto",sans-serif;font-size:17px;font-weight:500;color:var(--ink);line-height:1.2}
.footer-badge-rule{left:897px;top:2522px;width:210px;height:1px;background:#e2e2e2}
.footer-social{left:934px;top:2535px}
.footer-social .net{width:40px;height:40px}
.bottom-rule{left:300px;top:2600px;width:600px;height:1px;background:#e2e2e2}
.copyright{left:0;top:2623px;width:1200px;text-align:center;font-size:14px;color:#555}
.copyright b{color:#222;font-weight:400}
</style>
</head>
<body>

<header>
  <div class="abs topbar">
    <div class="social">
      <span class="net"><svg width="14" height="14" viewBox="0 0 14 14"><circle cx="3" cy="7" r="2" fill="#666"/><circle cx="11" cy="3" r="2" fill="#666"/><circle cx="11" cy="11" r="2" fill="#666"/><path d="M3 7l8-4M3 7l8 4" stroke="#666" stroke-width="1.2"/></svg></span>
      <span class="net"><svg width="14" height="14" viewBox="0 0 14 14"><circle cx="3" cy="7" r="2" fill="#666"/><circle cx="11" cy="3" r="2" fill="#666"/><circle cx="11" cy="11" r="2" fill="#666"/><path d="M3 7l8-4M3 7l8 4" stroke="#666" stroke-width="1.2"/></svg></span>
      <span class="net"><svg width="14" height="14" viewBox="0 0 14 14"><circle cx="3" cy="7" r="2" fill="#666"/><circle cx="11" cy="3" r="2" fill="#666"/><circle cx="11" cy="11" r="2" fill="#666"/><path d="M3 7l8-4M3 7l8 4" stroke="#666" stroke-width="1.2"/></svg></span>
    </div>
    <div class="contact-top">
      <div>
        <svg width="18" height="13" viewBox="0 0 18 13"><rect x="0" y="0" width="18" height="13" rx="1" fill="#555"/><path d="M1 1l8 6 8-6" stroke="#fff" stroke-width="1.4" fill="none"/></svg>
        hello@oaklineoffice.com
      </div>
      <div>
        <svg width="16" height="16" viewBox="0 0 24 24"><path fill="#555" d="M6.6 10.8a15 15 0 006.6 6.6l2.2-2.2a1 1 0 011-.25 11.4 11.4 0 003.6.57 1 1 0 011 1V20a1 1 0 01-1 1A17 17 0 013 4a1 1 0 011-1h3.5a1 1 0 011 1c0 1.25.2 2.45.57 3.6a1 1 0 01-.25 1z"/></svg>
        +1 555 014 2290
      </div>
    </div>
  </div>

  <div class="abs nav-rule" style="top:105px"></div>
  <div class="abs nav-rule" style="top:167px"></div>
  <nav class="abs nav nav-left"><a>HOME</a><a>ABOUT US</a><a>PRODUCT</a></nav>
  <nav class="abs nav nav-right"><a>FREE ESTIMATE</a><a>NEWS</a><a>CONTACT US</a></nav>
  <div class="abs brand-badge">Oakline<br>Office</div>
</header>

<section>
  <div class="abs hero" role="img" aria-label="Black mesh office chair beside a grey desk with monitor and phone in a bright office"></div>
  <div class="abs hero-arrow arrow-l"><svg width="12" height="14" viewBox="0 0 12 14"><path d="M6 1L1 7l5 6M11 1L6 7l5 6" stroke="#ddd" stroke-width="1.5" fill="none"/></svg></div>
  <div class="abs hero-arrow arrow-r"><svg width="12" height="14" viewBox="0 0 12 14"><path d="M1 1l5 6-5 6M6 1l5 6-5 6" stroke="#ddd" stroke-width="1.5" fill="none"/></svg></div>
</section>

<section>
  <h1 class="abs section-title" style="top:744px">WELCOME TO OAKLINE OFFICE</h1>
  <p class="abs intro">Lorem Ipsum is simply dummy text of the printing and typesetting industry. Lorem Ipsum has been the industry's standard dummy text ever since the 1500s, when an unknown printer took a galley of type and scrambled it to make a type specimen book. It has survived not only five centuries, but also the leap into electronic.</p>
  <div class="abs btn know-more">Know More</div>
  <div class="abs divider"></div>
</section>

<section>
  <h2 class="abs section-title" style="top:1076px">OUR PRODUCT</h2>

  <div class="abs product" style="left:78px;top:1157px"><div class="photo ph-chair" role="img" aria-label="Black curved cantilever chair"></div><div class="name">Chairs</div><div class="price">$25.89</div><div class="btn detail">Detail</div></div>
  <div class="abs product" style="left:343px;top:1157px"><div class="photo ph-cloth" role="img" aria-label="Stack of folded coloured cotton cloths"></div><div class="name">Cotton</div><div class="price">$25.89</div><div class="btn detail">Detail</div></div>
  <div class="abs product" style="left:609px;top:1157px"><div class="photo ph-safe" role="img" aria-label="Black burglary safe with open door"></div><div class="name">Burglary</div><div class="price">$25.89</div><div class="btn detail">Detail</div></div>
  <div class="abs product" style="left:873px;top:1157px"><div class="photo ph-table" role="img" aria-label="Dark curved side table"></div><div class="name">Table</div><div class="price">$25.89</div><div class="btn detail">Detail</div></div>

  <div class="abs product" style="left:78px;top:1486px"><div class="photo ph-chair" role="img" aria-label="Black chair with carved back"></div><div class="name">Chairs</div><div class="price">$25.89</div><div class="btn detail">Detail</div></div>
  <div class="abs product" style="left:343px;top:1486px"><div class="photo ph-scarf" role="img" aria-label="Folded grey cotton throw"></div><div class="name">Cotton</div><div class="price">$25.89</div><div class="btn detail">Detail</div></div>
  <div class="abs product" style="left:609px;top:1486px"><div class="photo ph-wood" role="img" aria-label="Tall dark brown wooden wardrobe"></div><div class="name">Wardrobe</div><div class="price">$25.89</div><div class="btn detail">Detail</div></div>
  <div class="abs product" style="left:873px;top:1486px"><div class="photo ph-table" role="img" aria-label="Round black pedestal table"></div><div class="name">Table</div><div class="price">$25.89</div><div class="btn detail">Detail</div></div>
</section>

<section class="abs newsletter">
  <div class="label">SIGN UP NEWSLETTER</div>
  <div class="email">Enter Your Email</div>
  <div class="btn subscribe">Subscribe</div>
</section>

<section>
  <div class="abs work work-a" role="img" aria-label="White office interior with glass partitions and yellow lounge chair"></div>
  <div class="abs work work-b" role="img" aria-label="Soft white desk setting with plant">
    <div class="caption">LATEST WORK</div>
    <div class="btn view">View</div>
  </div>
  <div class="abs work work-c" role="img" aria-label="Reception area with wooden front desk and grey seating"></div>
</section>

<footer>
  <div class="abs footer-rule"></div>

  <div class="abs f-col" style="left:78px">
    <h4>USEFULL LINKS</h4>
    <ul><li>Home</li><li>About Us</li><li>Product</li><li>Free Estimate</li><li>News</li><li>Contact Us</li></ul>
  </div>
  <div class="abs f-col" style="left:343px">
    <h4>OUR PRODUCT</h4>
    <ul><li>Chairs</li><li>Tables</li><li>Burglary</li><li>Cotton</li><li>Wardrobe</li></ul>
  </div>
  <div class="abs f-col" style="left:609px">
    <h4>GET IN TOUCH</h4>
    <div class="touch-row">
      <svg width="16" height="20" viewBox="0 0 16 20"><path d="M8 1a6 6 0 00-6 6c0 5 6 12 6 12s6-7 6-12a6 6 0 00-6-6z" stroke="#555" stroke-width="1.4" fill="none"/><circle cx="8" cy="7" r="2" stroke="#555" stroke-width="1.4" fill="none"/></svg>
      <div><strong>OAKLINE OFFICE</strong>Lorem ipsum dolor amet simple.</div>
    </div>
    <div class="touch-row">
      <svg width="16" height="16" viewBox="0 0 24 24"><path d="M6.6 10.8a15 15 0 006.6 6.6l2.2-2.2a1 1 0 011-.25 11.4 11.4 0 003.6.57 1 1 0 011 1V20a1 1 0 01-1 1A17 17 0 013 4a1 1 0 011-1h3.5a1 1 0 011 1c0 1.25.2 2.45.57 3.6a1 1 0 01-.25 1z" stroke="#555" stroke-width="1.6" fill="none"/></svg>
      <div>+1 555 014 2291</div>
    </div>
    <div class="touch-row">
      <svg width="16" height="16" viewBox="0 0 16 16"><rect x="3" y="1" width="10" height="5" stroke="#555" stroke-width="1.3" fill="none"/><rect x="1" y="6" width="14" height="6" rx="1" stroke="#555" stroke-width="1.3" fill="none"/><rect x="4" y="10" width="8" height="5" stroke="#555" stroke-width="1.3" fill="#fff"/></svg>
      <div>+1 555 014 2291</div>
    </div>
    <div class="touch-row">
      <svg width="16" height="13" viewBox="0 0 18 13"><rect x="1" y="1" width="16" height="11" stroke="#555" stroke-width="1.4" fill="none"/><path d="M1 1l8 6 8-6" stroke="#555" stroke-width="1.4" fill="none"/></svg>
      <div>hello@oaklineoffice.com</div>
    </div>
  </div>

  <div class="abs footer-badge">Oakline<br>Office</div>
  <div class="abs footer-badge-rule"></div>
  <div class="abs social footer-social">
    <span class="net"><svg width="16" height="16" viewBox="0 0 14 14"><circle cx="3" cy="7" r="2" fill="#666"/><circle cx="11" cy="3" r="2" fill="#666"/><circle cx="11" cy="11" r="2" fill="#666"/><path d="M3 7l8-4M3 7l8 4" stroke="#666" stroke-width="1.2"/></svg></span>
    <span class="net"><svg width="16" height="16" viewBox="0 0 14 14"><circle cx="3" cy="7" r="2" fill="#666"/><circle cx="11" cy="3" r="2" fill="#666"/><circle cx="11" cy="11" r="2" fill="#666"/><path d="M3 7l8-4M3 7l8 4" stroke="#666" stroke-width="1.2"/></svg></span>
    <span class="net"><svg width="16" height="16" viewBox="0 0 14 14"><circle cx="3" cy="7" r="2" fill="#666"/><circle cx="11" cy="3" r="2" fill="#666"/><circle cx="11" cy="11" r="2" fill="#666"/><path d="M3 7l8-4M3 7l8 4" stroke="#666" stroke-width="1.2"/></svg></span>
  </div>

  <div class="abs bottom-rule"></div>
  <p class="abs copyright">© 2016 <b>Oakline Office</b> -&nbsp; All rights reserved.</p>
</footer>

</body>
</html>
```